Awesome business card design needed

We need a new business card design to go with our new logo.
We are a web development agency that specialises in highly complex back-end integrations as opposed to design, our customers are retailers, hotels, hospitals and any other organisation that has a large online marketing department.
Take a look at our website - www.brenoloft.com for some inspiration.
We want our new business cards to exude class, professionalism and style.
We are likely to choose a high-end card to print them on but we want the design of the card itself to really turn heads.
We have no specific colour requirements, the logo as you will see is a turquoise colour R89 G171 B167 #59aba7 but it can also be in white if you want to make the colour of the card something different.
The information on the card should be:
Name
Position
Tel
email
Potentially a double sided card could have our web address, twitter and FB links.

```html
<!DOCTYPE html>
<html lang="en">
<head>
<meta charset="utf-8">
<title>Brenoloft Business Card</title>
<link rel="stylesheet" href="https://fonts.googleapis.com/css2?family=Jost:wght@400;500;700&display=swap">
<style>
  :root {
    --teal: #59aba7;
    --white: #ffffff;
    --ink: #3a3a3a;
    --rule: #b9b9b9;
    --backdrop: #e9e9ee;
  }
  * { margin: 0; padding: 0; box-sizing: border-box; }
  html, body { width: 1200px; height: 987px; overflow: hidden; }
  body {
    background: var(--backdrop);
    font-family: "Jost", sans-serif;
    position: relative;
  }
  .card {
    position: absolute;
    width: 580px;
    height: 331px;
    border-radius: 28px;
    overflow: hidden;
    box-shadow: 0 10px 30px rgba(0,0,0,0.12);
  }
  /* Back side */
  .card--back {
    left: 560px; top: 80px;
    background: var(--teal);
    color: var(--white);
  }
  .card--back .wordmark {
    position: absolute;
    left: 60px; top: 60px;
    font-size: 104px;
    font-weight: 700;
    letter-spacing: 2px;
    line-height: 1;
    color: var(--white);
  }
  .card--back .follow {
    position: absolute;
    left: 64px; top: 210px;
    display: flex; align-items: center; gap: 12px;
    font-size: 19px; letter-spacing: 1px;
  }
  .social-square {
    width: 30px; height: 30px;
    border-radius: 6px;
    background: rgba(255,255,255,0.85);
  }
  .card--back .web {
    position: absolute;
    left: 64px; top: 256px;
    font-size: 19px; letter-spacing: 2px;
  }
  /* Front side */
  .card--front {
    left: 60px; top: 560px;
    background: var(--white);
    color: var(--ink);
  }
  .card--front .wordmark {
    position: absolute;
    left: 40px; top: 30px;
    font-size: 86px;
    font-weight: 700;
    letter-spacing: 2px;
    line-height: 1;
    color: var(--teal);
  }
  .contact-list {
    position: absolute;
    left: 40px; top: 150px;
    list-style: none;
    font-size: 17px;
  }
  .contact-list li {
    display: flex; align-items: center; gap: 10px;
    height: 26px;
  }
  .contact-list svg { width: 14px; height: 14px; flex: none; }
  .divider {
    position: absolute;
    left: 0; right: 0; top: 240px;
    height: 2px;
    background: linear-gradient(90deg, rgba(185,185,185,0.2), var(--rule));
  }
  .person {
    position: absolute;
    right: 36px; top: 172px;
    text-align: right;
  }
  .person .name {
    font-size: 26px; font-weight: 500;
    color: var(--teal); line-height: 1.1;
  }
  .person .position { font-size: 19px; line-height: 1.3; }
  .address {
    position: absolute;
    right: 36px; top: 252px;
    text-align: right;
    font-size: 19px; line-height: 1.25;
  }
</style>
</head>
<body>
  <section class="card card--back">
    <div class="wordmark">brenoloft</div>
    <div class="follow">
      <span>Follow Us On:</span>
      <span class="social-square"></span>
      <span class="social-square"></span>
    </div>
    <div class="web">www.brenoloft.com</div>
  </section>

  <section class="card card--front">
    <div class="wordmark">brenoloft</div>
    <ul class="contact-list">
      <li>
        <svg viewBox="0 0 14 14"><circle cx="7" cy="7" r="6.5" fill="none" stroke="var(--teal)"/><path d="M4.5 4 L6 5.5 L5.3 6.4 Q6.5 8 7.6 8.7 L8.5 8 L10 9.5 L9 10.5 Q5.5 9.5 3.5 5 Z" fill="var(--teal)"/></svg>
        123-456-7890
      </li>
      <li>
        <svg viewBox="0 0 14 14"><rect x="1" y="3" width="12" height="8" rx="1" fill="var(--teal)"/><path d="M1 3 L7 8 L13 3" fill="none" stroke="#fff" stroke-width="1"/></svg>
        info@brenoloft.com
      </li>
      <li>
        <svg viewBox="0 0 14 14"><circle cx="7" cy="7" r="6" fill="var(--teal)"/><path d="M1 7 H13 M7 1 V13 M2.5 4 H11.5 M2.5 10 H11.5" stroke="#fff" stroke-width="0.8"/><ellipse cx="7" cy="7" rx="2.6" ry="6" fill="none" stroke="#fff" stroke-width="0.8"/></svg>
        www.brenoloft.com
      </li>
    </ul>
    <div class="person">
      <div class="name">Your Name</div>
      <div class="position">Position</div>
    </div>
    <div class="divider"></div>
    <div class="address">Street Name, City Name<br>State Zip Code</div>
  </section>
</body>
</html>
```